Stationery Design Project

We need, stationary designs for a store of children and juvenile furniture.
we have the logo. also need tags for the furniture with enought space to include description and options , maybe a 4" x 6" tag.

Target Market(s)

Parents of childrens and teens

Industry/Entity Type

Store

```html
<!DOCTYPE html>
<html lang="en">
<head>
<meta charset="utf-8">
<title>Nestling Rooms – Business Card</title>
<link href="https://fonts.googleapis.com/css2?family=Arimo:wght@400;700&family=Questrial&display=swap" rel="stylesheet">
<style>
  :root {
    --backdrop: #5f5f61;
    --card: #fbfbfa;
    --teal: #4fadbc;
    --ink: #6d6e70;
    --ink-soft: #7a7b7d;
  }
  * { box-sizing: border-box; margin: 0; padding: 0; }
  html, body {
    width: 1200px;
    height: 800px;
    overflow: hidden;
    background: var(--backdrop);
  }
  .canvas {
    position: relative;
    width: 1200px;
    height: 800px;
    display: flex;
    align-items: center;
    justify-content: center;
  }
  .business-card {
    position: relative;
    width: 840px;
    height: 480px;
    background: var(--card);
    box-shadow: 0 18px 40px rgba(0, 0, 0, 0.35);
    overflow: hidden;
  }
  .edge-band {
    position: absolute;
    left: 0;
    top: 0;
    width: 60px;
    height: 480px;
  }
  .brand {
    position: absolute;
    top: 96px;
    left: 0;
    right: 0;
    display: flex;
    align-items: center;
    justify-content: center;
    gap: 16px;
  }
  .brand-mark {
    width: 26px;
    height: 26px;
    background: var(--teal);
  }
  .brand-name {
    font-family: "Questrial", sans-serif;
    font-size: 54px;
    letter-spacing: 2px;
    color: var(--ink);
  }
  .holder {
    position: absolute;
    top: 232px;
    left: 0;
    right: 0;
    text-align: center;
  }
  .holder-name {
    font-family: "Questrial", sans-serif;
    font-size: 26px;
    letter-spacing: 1px;
    color: var(--ink);
    font-weight: 400;
  }
  .holder-role {
    font-family: "Arimo", sans-serif;
    font-size: 17px;
    color: var(--teal);
    margin-top: 2px;
  }
  .contact {
    position: absolute;
    bottom: 58px;
    left: 0;
    right: 0;
    text-align: center;
    font-family: "Arimo", sans-serif;
    font-size: 17px;
    line-height: 1.7;
    color: var(--ink-soft);
  }
  .contact-label {
    color: var(--teal);
    font-weight: 700;
    margin-left: 10px;
  }
  .contact-label:first-child { margin-left: 0; }
</style>
</head>
<body>
  <main class="canvas">
    <article class="business-card">
      <svg class="edge-band" viewBox="0 0 60 480" aria-hidden="true">
        <path d="M0 0 C40 120 40 360 0 480 Z" fill="var(--teal)"/>
      </svg>

      <header class="brand">
        <span class="brand-mark" aria-hidden="true"></span>
        <span class="brand-name">Nestling Rooms</span>
      </header>

      <section class="holder">
        <h1 class="holder-name">MARA ELLISON</h1>
        <p class="holder-role">Manager</p>
      </section>

      <address class="contact">
        <p>Lantern Way, Hollowbrook NSW 2999</p>
        <p>
          <span class="contact-label">Tel:</span> +61 2 5550 1200
          <span class="contact-label">Fax:</span> +61 2 5550 1210
          <span class="contact-label">Email:</span> hello@nestlingrooms.com
        </p>
      </address>
    </article>
  </main>
</body>
</html>
```